Modern and Simple Supplement Label Design

We are looking for a Professional Graphic Designer who can design eye-catching and unique supplement label. We are supplement company who are sourcing different supplement products. I would like the design to be simple and with few colorsThe final design should communicate strength and growthI attached some samples for inspiration

Target Market(s)

Supplement Market - Collagen Supplements

Industry/Entity Type

Supplement

Font styles to use
Serif
Sans Serif

Colors

Designer to choose colors to be used in the design.

Requirements
Must have
• Front (Please search on Brindleport Collagen to get inspiration how to put together the front text)
• Logo: Vellow Naturals
• Product Name: Omni Dermal Capsules
• Hydrolyzed type I II III V & X Collagen
• Dietary Supplements - 90 capsules
• Support Joints & bones
• Rejuvenate Skin
• Promotes Healthy Hair & Nails
• One right side supplement fact and left side precaution and instruction content. ( Please find the content of the right and left side of the bottle attached)
Nice to have
• Nice to have something that shows elements bring together to create something strong or beautiful. Our brand name is Vellow Naturals. Vellow is an assembly of beams or other elements that creates a rigid structure. This is to show our supplements help to provide the elements to have strong and healthy life

```html
<!DOCTYPE html>
<html lang="en">
<head>
<meta charset="utf-8">
<title>Vellow Naturals – Omni Dermal Capsules Label</title>
<link rel="stylesheet" href="https://fonts.googleapis.com/css2?family=Montserrat:wght@300;400;500;700&family=Oswald:wght@500&family=Roboto+Condensed:wght@400&display=swap">
<style>
  :root {
    --paper: #ffffff;
    --ink: #5b5b5b;
    --ink-dark: #3a3a3a;
    --gold: #f2a81c;
    --gold-light: #f8c53a;
    --gold-deep: #e08d12;
    --brick: #a8321c;
    --silver: #d9d9d9;
    --silver-light: #f1f1f1;
    --pill-grey: #8a8a8a;
    --icon-grey: #c9c9c9;
  }
  * { box-sizing: border-box; margin: 0; padding: 0; }
  html, body { width: 1200px; height: 1164px; overflow: hidden; background: var(--paper); }
  body { font-family: "Montserrat", sans-serif; color: var(--ink); position: relative; }

  .label {
    position: absolute; left: 100px; top: 200px; width: 1000px; height: 760px;
    background: var(--paper); overflow: hidden;
    border-top: 10px solid var(--silver); border-bottom: 10px solid var(--silver);
  }

  .brand {
    position: absolute; top: 40px; left: 0; right: 0; height: 150px;
    display: flex; align-items: center; justify-content: center; gap: 22px;
  }
  .brand-dot { width: 70px; height: 70px; border-radius: 50%; background: var(--gold); }
  .brand-name {
    font-family: "Montserrat", sans-serif; font-weight: 700; font-size: 58px;
    line-height: 1; color: var(--ink); letter-spacing: 1px;
  }

  .title-band {
    position: absolute; top: 210px; left: 0; right: 0; height: 230px;
    background: linear-gradient(180deg, var(--gold-light), var(--gold) 55%, var(--gold-deep));
    text-align: center; color: var(--paper);
  }
  .type-pill {
    position: absolute; top: -22px; left: 50%; transform: translateX(-50%);
    background: var(--pill-grey); color: var(--paper); white-space: nowrap;
    font-weight: 700; font-size: 28px; letter-spacing: 4px;
    padding: 8px 44px; border-radius: 30px; border: 3px solid var(--silver-light);
  }
  .product-line { position: absolute; top: 48px; left: 0; right: 0; font-weight: 300; font-size: 60px; letter-spacing: 3px; line-height: 1; }
  .product-name { position: absolute; top: 108px; left: 0; right: 0; font-weight: 500; font-size: 104px; letter-spacing: 2px; line-height: 1; }

  .badge { position: absolute; width: 60px; height: 68px; }
  .badge-left { left: -30px; }
  .badge-right { right: -30px; }

  .benefits {
    position: absolute; top: 440px; left: 0; right: 0; height: 170px; text-align: center;
  }
  .tagline {
    margin-top: 12px; font-family: "Oswald", sans-serif; font-weight: 500;
    font-size: 26px; line-height: 32px; color: var(--brick); letter-spacing: 1px;
  }
  .benefit-list { list-style: none; display: flex; justify-content: center; gap: 20px; margin-top: 10px; }
  .benefit { width: 210px; display: flex; flex-direction: column; align-items: center; gap: 6px; }
  .benefit-icon { width: 52px; height: 62px; border-radius: 26px; background: var(--icon-grey); }
  .benefit-label { font-family: "Roboto Condensed", sans-serif; font-size: 23px; line-height: 28px; color: var(--ink-dark); white-space: nowrap; }

  .dose-band {
    position: absolute; top: 610px; left: 0; right: 0; height: 90px;
    background: linear-gradient(180deg, var(--gold-light), var(--gold));
    display: flex; align-items: center; justify-content: center;
  }
  .dose-pill {
    background: var(--paper); color: var(--brick); border-radius: 14px; white-space: nowrap;
    font-family: "Oswald", sans-serif; font-weight: 500; font-size: 28px;
    padding: 8px 34px; letter-spacing: 1px;
  }

  .footer {
    position: absolute; top: 700px; left: 0; right: 0; height: 50px;
    background: linear-gradient(180deg, var(--silver-light), var(--silver));
    display: flex; align-items: center; justify-content: center;
    font-family: "Oswald", sans-serif; font-weight: 500; font-size: 28px; color: var(--ink-dark);
  }
</style>
</head>
<body>
  <main class="label">
    <header class="brand">
      <span class="brand-dot"></span>
      <span class="brand-name">vellow naturals</span>
    </header>

    <section class="title-band">
      <span class="type-pill">HYDROLYZED</span>
      <h1 class="product-line">OMNI DERMAL</h1>
      <h2 class="product-name">CAPSULES</h2>

      <svg class="badge badge-left" style="top:20px" viewBox="0 0 60 68"><polygon points="30,2 58,18 58,50 30,66 2,50 2,18" fill="var(--paper)" stroke="var(--brick)" stroke-width="4"/></svg>
      <svg class="badge badge-left" style="top:100px" viewBox="0 0 60 68"><polygon points="30,2 58,18 58,50 30,66 2,50 2,18" fill="var(--paper)" stroke="var(--brick)" stroke-width="4"/></svg>
      <svg class="badge badge-right" style="top:20px" viewBox="0 0 60 68"><polygon points="30,2 58,18 58,50 30,66 2,50 2,18" fill="var(--paper)" stroke="var(--brick)" stroke-width="4"/></svg>
      <svg class="badge badge-right" style="top:100px" viewBox="0 0 60 68"><polygon points="30,2 58,18 58,50 30,66 2,50 2,18" fill="var(--paper)" stroke="var(--brick)" stroke-width="4"/></svg>
    </section>

    <section class="benefits">
      <p class="tagline">— POWERFUL FORMULA FOR OVERALL HEALTH —</p>
      <ul class="benefit-list">
        <li class="benefit"><span class="benefit-icon" role="img" aria-label="Joints icon"></span><span class="benefit-label">Supports Joints</span></li>
        <li class="benefit"><span class="benefit-icon" role="img" aria-label="Bones icon"></span><span class="benefit-label">Strong Bones</span></li>
        <li class="benefit"><span class="benefit-icon" role="img" aria-label="Skin icon"></span><span class="benefit-label">Rejuvenate Skin</span></li>
        <li class="benefit"><span class="benefit-icon" role="img" aria-label="Hair and nails icon"></span><span class="benefit-label">Hair &amp; Nails</span></li>
      </ul>
    </section>

    <section class="dose-band">
      <p class="dose-pill">TYPE I, II, III, V &amp; X COLLAGEN</p>
    </section>

    <footer class="footer">DIETARY SUPPLEMENTS - 90 CAPSULES</footer>
  </main>
</body>
</html>
```